Internet Service Tech provider product flyer redesign - High Rise WIFI

We have created the attached flyer in Word and also attached a PDF. All the content is correct. We just need a complete re-design of the flyer with new relevant hi-res images (based on content) and a more streamlined/cleaner layout.

This product is an entire in-building WIFI system for Body's Corporate in High Rise buildings.

We are a Brisbane-based internet tech company that specialises in providing solutions for High Rise buildings

Body text style - Helvetica Light

Internet

```html
<!DOCTYPE html>
<html lang="en">
<head>
<meta charset="utf-8">
<title>High Rise WIFI – Our Technologies</title>
<link href="https://fonts.googleapis.com/css2?family=Oswald:wght@500;600&family=Arimo:wght@400;700&display=swap" rel="stylesheet">
<style>
  :root {
    --navy: #1b2340;
    --band: #2d5670;
    --red: #d9262c;
    --red-dark: #a3151b;
    --heading-red: #e03a2f;
    --ink: #2e2e2e;
    --white: #ffffff;
    --photo-teal: #1f6f78;
    --photo-blue: #1a2f5c;
    --photo-amber: #e49a3b;
  }
  html, body { margin: 0; padding: 0; overflow: hidden; background: var(--white); }
  .flyer {
    position: relative;
    width: 871px;
    height: 1200px;
    overflow: hidden;
    background: var(--white);
    font-family: "Arimo", Helvetica, Arial, sans-serif;
  }
  .layer { position: absolute; inset: 0; width: 871px; height: 1200px; }
  .contact { position: absolute; left: 507px; top: 30px; }
  .contact-title {
    margin: 0 0 10px;
    font-family: "Oswald", "Arial Narrow", sans-serif;
    font-weight: 600;
    font-size: 30px;
    letter-spacing: 0.5px;
    color: var(--heading-red);
  }
  .contact-line { margin: 0; font-size: 16.5px; line-height: 22px; color: var(--white); }
  .section-title {
    position: absolute; left: 512px; top: 280px; margin: 0;
    font-weight: 700; font-size: 28px; color: var(--red);
  }
  .feature-label {
    position: absolute;
    font-family: "Oswald", "Arial Narrow", sans-serif;
    font-weight: 500;
    font-size: 23px;
    line-height: 33px;
    color: var(--white);
    text-align: center;
    letter-spacing: 0.5px;
    transform: translate(-50%, -50%);
    white-space: nowrap;
  }
  .feature-item {
    position: absolute; margin: 0;
    font-size: 15px; line-height: 18px; color: var(--ink);
    white-space: nowrap;
  }
  .brand-name {
    position: absolute; right: 52px; top: 1136px; margin: 0;
    font-family: "Oswald", "Arial Narrow", sans-serif;
    font-weight: 600; font-size: 30px; color: var(--navy); letter-spacing: 0.5px;
  }
</style>
</head>
<body>
<div class="flyer">

  <svg class="layer city-photo" viewBox="0 0 871 1200" role="img" aria-label="Night city skyline with illuminated high-rise towers and light trails from traffic">
    <defs>
      <linearGradient id="cityTone" x1="0" y1="0" x2="0.4" y2="1">
        <stop offset="0" stop-color="var(--photo-blue)"/>
        <stop offset="0.3" stop-color="var(--photo-teal)"/>
        <stop offset="0.55" stop-color="#3f8f8a"/>
        <stop offset="0.72" stop-color="var(--photo-amber)"/>
        <stop offset="0.86" stop-color="#7a4a2a"/>
        <stop offset="1" stop-color="#3a3a40"/>
      </linearGradient>
    </defs>
    <path d="M0,0 H365 C430,300 420,800 175,1200 H0 Z" fill="url(#cityTone)"/>
  </svg>

  <svg class="layer frame-shapes" viewBox="0 0 871 1200" aria-hidden="true">
    <defs>
      <radialGradient id="badgeRed" cx="0.4" cy="0.35" r="0.7">
        <stop offset="0" stop-color="var(--red)"/>
        <stop offset="1" stop-color="var(--red-dark)"/>
      </radialGradient>
    </defs>
    <path class="header-band" d="M372,0 H871 V212 Q640,196 412,128 Z" fill="var(--navy)"/>
    <path class="curve-band" d="M396,0 C461,300 451,800 206,1200" fill="none" stroke="var(--band)" stroke-width="22"/>
    <g class="feature-badges" fill="url(#badgeRed)" stroke="var(--white)" stroke-width="7">
      <circle cx="399" cy="436" r="80"/>
      <circle cx="350" cy="673" r="80"/>
      <circle cx="252" cy="930" r="82"/>
    </g>
  </svg>

  <div class="contact">
    <h2 class="contact-title">GET IN TOUCH</h2>
    <p class="contact-line">info@skylinkfibre.com.au</p>
    <p class="contact-line">www.skylinkfibre.com.au</p>
  </div>

  <h1 class="section-title">Our Technologies</h1>

  <div class="feature-label" style="left:399px;top:436px">BULK<br>SUPPLY</div>
  <div class="feature-label" style="left:350px;top:673px">HD WIFI</div>
  <div class="feature-label" style="left:252px;top:930px">AUTOMATED<br>BILLING</div>

  <p class="feature-item" style="left:508px;top:346px">Licensed telecommunications and internet<br>service carrier</p>
  <p class="feature-item" style="left:506px;top:391px">Technology designed for multiresident<br>usage</p>
  <p class="feature-item" style="left:504px;top:436px">Corporate backup connections included</p>
  <p class="feature-item" style="left:503px;top:462px">Up to 1000Mbps speed downloads/uploads</p>
  <p class="feature-item" style="left:501px;top:488px">1000Mbps embedded network infrastructure</p>
  <p class="feature-item" style="left:498px;top:514px">Professional service guaranteed</p>
  <p class="feature-item" style="left:495px;top:540px">99.999% uptime service level agreements</p>

  <p class="feature-item" style="left:484px;top:616px">High definition output up to 30+dBm</p>
  <p class="feature-item" style="left:482px;top:642px">Multi-radio design</p>
  <p class="feature-item" style="left:480px;top:668px">10/100/1000 Ethernet LAN connection</p>
  <p class="feature-item" style="left:474px;top:694px">Up to 300Mbps data transfer rates – per radio</p>
  <p class="feature-item" style="left:468px;top:720px">LED signal strength display</p>
  <p class="feature-item" style="left:460px;top:746px">SNMP remote management and configuration</p>
  <p class="feature-item" style="left:455px;top:772px">Stealth design to blend into building aesthetics</p>

  <p class="feature-item" style="left:426px;top:858px">Tier 1 PCS-DSS certified</p>
  <p class="feature-item" style="left:421px;top:884px">Branded web portal for payment gateway</p>
  <p class="feature-item" style="left:412px;top:910px">Fast payment processing</p>
  <p class="feature-item" style="left:403px;top:936px">SSL security for payment transactions</p>
  <p class="feature-item" style="left:393px;top:962px">Local, friendly, and professional support</p>
  <p class="feature-item" style="left:382px;top:988px">Guest self service and payment</p>
  <p class="feature-item" style="left:373px;top:1014px">Get paid 24/7</p>

  <p class="brand-name">SKYLINK FIBRE</p>

</div>
</body>
</html>
```